Stationery Design + Business Cards

Stationary (letterhead as A4 210x297mm and Letter 8.5"x11", preferably both master page + 2nd pages)

Also need business cards, standard size 50x88mm, can be vertical or horizontal.

You can use a front/back design for the business cards, or front only.

Looking at the uploaded file (devank, you already have that), I want it to use the first logo on the list (4 colors).

Alternative, try the grayscale version (second file).

I need the following information on the business card (in no particular order, let me know what you come up with): 

Firstname Lastlame 
Title 

Mobile +1 555-204-7391 

VelaMorn, Inc. 
24851 Birchwood Ridge Passage 
Ashcombe, OH 46099 
Tel. +1 555-368-4172 
Fax +1 555-619-0834 

Web: www.velamorn.example 
Twitter: twitter/VelaMorn or @VelaMorn 
Facebook: facebook.com/VelaMorn 

For letterhead, just the company name, address + phone number & fax number 

If you think the phone/fax or something else should not be on the business cards, or something could be missing, let me know.

```html
<!DOCTYPE html>
<html lang="en">
<head>
<meta charset="utf-8">
<title>VelaMorn Letterhead</title>
<link href="https://fonts.googleapis.com/css2?family=Source+Sans+3:wght@400&display=swap" rel="stylesheet">
<style>
  :root {
    --backdrop: #ffffff;
    --paper: #ffffff;
    --paper-edge: #d4d4d4;
    --brand-grey: #5a5a5a;
    --band-grey: #6b6b6b;
    --band-text: #f2f2f2;
    --mark-grey: #7a7a7a;
  }
  * { margin: 0; padding: 0; box-sizing: border-box; }
  html, body {
    width: 1200px;
    height: 960px;
    overflow: hidden;
    background: var(--backdrop);
    font-family: "Source Sans 3", "Myriad Pro", Arial, sans-serif;
  }
  .canvas {
    position: relative;
    width: 1200px;
    height: 960px;
  }
  .letterhead {
    position: absolute;
    left: 278px;
    top: 49px;
    width: 663px;
    height: 859px;
    background: var(--paper);
    border: 1px solid var(--paper-edge);
    box-shadow: 0 1px 4px rgba(0, 0, 0, 0.25);
  }
  .brand-header {
    position: absolute;
    left: 52px;
    top: 52px;
    display: flex;
    align-items: center;
    gap: 6px;
  }
  .brand-dot {
    width: 40px;
    height: 40px;
    border-radius: 50%;
    background: var(--mark-grey);
  }
  .brand-name {
    font-size: 38px;
    line-height: 1;
    color: var(--brand-grey);
    letter-spacing: 0.2px;
  }
  .footer-band {
    position: absolute;
    left: 52px;
    top: 801px;
    width: 488px;
    height: 30px;
    background: var(--band-grey);
    display: flex;
    align-items: center;
    padding: 8px 0 0 9px;
  }
  .footer-contact {
    font-size: 8.6px;
    line-height: 1;
    color: var(--band-text);
    white-space: nowrap;
  }
  .footer-brand {
    position: absolute;
    left: 527px;
    top: 811px;
    display: flex;
    align-items: center;
    gap: 3px;
    background: var(--paper);
    padding: 0 2px;
  }
  .footer-brand .brand-dot {
    width: 18px;
    height: 18px;
  }
  .footer-brand .brand-name {
    font-size: 14.5px;
  }
</style>
</head>
<body>
  <div class="canvas">
    <main class="letterhead">
      <header class="brand-header">
        <span class="brand-dot"></span>
        <span class="brand-name">VelaMorn</span>
      </header>

      <footer>
        <div class="footer-band">
          <p class="footer-contact">VelaMorn, Inc. &nbsp;|&nbsp; 24851 Birchwood Ridge Passage &nbsp;|&nbsp; Ashcombe, OH 46099 &nbsp;|&nbsp; Tel. +1 555-368-4172 &nbsp;|&nbsp; Fax +1 555-619-0834</p>
        </div>
        <div class="footer-brand">
          <span class="brand-dot"></span>
          <span class="brand-name">VelaMorn</span>
        </div>
      </footer>
    </main>
  </div>
</body>
</html>
```